Driver License Monitoring Application Marketing Website

We need a new web design for our web application. The product is called "RoadPermitGuard." We provide a driver license monitoring service to companies and local government bodies with driver fleets. Our current website is available at www.RoadPermitGuard-example.com.

I prefer a clean, single-page design with good SEO. Attached are some PDFs with data about the project.

Target Market(s)

Companies with driver fleets, local government.

Industry/Entity Type

Government

Coding

Coded - Design and coding required

Number of Pages Required

1 page

Colors
000000

Requirements
Must have
• Content from current www.RoadPermitGuard-example.com and attached PDFs.
Nice to have
• Prefer a simple Bootstrap or similar design for easy editing.
• Room for a simple video explanation of how the product works (we don't have an actual video yet)

```html
<!DOCTYPE html>
<html lang="en">
<head>
<meta charset="utf-8">
<title>RoadPermitGuard – Florida Driver License Monitoring</title>
<link href="https://fonts.googleapis.com/css2?family=Source+Sans+3:wght@300;400;600;700&family=PT+Serif:wght@400&display=swap" rel="stylesheet">
<style>
:root{
  --red:#c4262e;
  --red-dark:#a81e25;
  --ink:#1f2126;
  --text:#55585e;
  --muted:#8a8d92;
  --line:#e3e4e6;
  --white:#ffffff;
  --dark:#2a2c31;
  --footer:#1b1c1f;
  --link:#3a8fd3;
}
*{box-sizing:border-box;margin:0;padding:0}
html,body{width:1200px;height:5076px;overflow:hidden}
body{font-family:"Source Sans 3",Arial,sans-serif;color:var(--text);background:var(--white);position:relative}
.section{position:absolute;left:0;width:1200px}
.brand{font-family:"Source Sans 3",Arial,sans-serif;font-weight:700;color:var(--white);font-size:25px;letter-spacing:.5px}

/* hero */
.hero{top:0;height:840px;background:linear-gradient(160deg,#4a5560 0%,#2c333b 45%,#3a2224 75%,#1d1f22 100%)}
.hero-photo{position:absolute;inset:0;background:radial-gradient(ellipse at 80% 55%,rgba(170,30,36,.55),transparent 45%),linear-gradient(180deg,rgba(90,110,130,.35),rgba(0,0,0,.35))}
.nav{position:absolute;top:40px;left:100px;right:100px;display:flex;align-items:center;justify-content:space-between}
.nav-links{display:flex;gap:38px;align-items:center;list-style:none}
.nav-links li{color:var(--white);font-size:14px;letter-spacing:1px;text-transform:uppercase}
.search{width:30px;height:30px;border:2px solid rgba(255,255,255,.7);border-radius:50%;display:flex;align-items:center;justify-content:center}
.hero-kicker{position:absolute;top:270px;width:100%;text-align:center;color:#e8e8e8;font-family:"PT Serif",Georgia,serif;font-style:italic;font-size:17px}
.hero-kicker::after{content:"";display:block;width:120px;height:1px;background:rgba(255,255,255,.6);margin:12px auto 0}
.hero h1{position:absolute;top:330px;width:100%;text-align:center;color:var(--white);font-weight:300;font-size:70px;line-height:84px}
.hero-sub{position:absolute;top:512px;width:100%;text-align:center;color:var(--white);font-family:"PT Serif",Georgia,serif;font-size:25px;line-height:32px}
.btn{display:inline-block;background:var(--red);color:var(--white);font-size:13px;font-weight:700;letter-spacing:1.5px;text-transform:uppercase;padding:13px 30px;border-radius:22px}
.hero .btn{position:absolute;top:658px;left:50%;transform:translateX(-50%)}

/* intro */
.intro{top:840px;height:1204px}
.section-title{text-align:center;color:var(--ink);font-weight:700;font-size:32px}
.intro .section-title{margin-top:95px}
.intro-text{width:1000px;margin:30px auto 0;text-align:center;font-size:16px;line-height:26px}
.intro-art{position:absolute;top:420px;left:260px;width:680px;height:250px;background:linear-gradient(90deg,#e9ecef 0%,#f4f5f6 45%,#e8832c 60%,#d9482b 80%,#f0b23a 100%);border-radius:4px}
.services{position:absolute;top:765px;left:120px;width:960px;display:flex;justify-content:space-between}
.service{width:270px;text-align:center}
.service-icon{width:78px;height:78px;border:1px solid var(--line);border-radius:50%;margin:0 auto;display:flex;align-items:center;justify-content:center}
.service h3{margin-top:30px;font-size:14px;letter-spacing:2px;color:var(--ink);font-weight:600}
.service p{margin-top:14px;font-size:15px;line-height:22px}
.read-more{display:inline-block;margin-top:36px;color:var(--link);font-size:12px}

/* question band */
.question{top:2044px;height:483px;background:linear-gradient(100deg,#d6d8db 0%,#6c7078 22%,#3a3d42 45%,#2e3035 100%)}
.question-art{position:absolute;left:0;top:0;width:420px;height:483px;background:linear-gradient(120deg,#e8e9eb,#9ea2a8 60%,rgba(60,62,66,0));}
.question-kicker{position:absolute;top:60px;left:310px;color:var(--white);font-size:18px;font-weight:600}
.question h2{position:absolute;top:100px;left:260px;width:720px;text-align:center;color:var(--white);font-weight:300;font-size:44px;line-height:52px}
.devices-art{position:absolute;top:230px;left:600px;width:440px;height:250px;background:linear-gradient(135deg,#f2f2f2,#c9ccd0);border-radius:6px}

/* features */
.features{top:2527px;height:1655px}
.features .first-title{margin-top:200px}
.feature-grid{position:absolute;left:205px;width:800px;display:grid;grid-template-columns:repeat(3,255px);column-gap:30px;row-gap:60px}
.feature h4{display:flex;align-items:center;gap:9px;color:var(--ink);font-size:17px;font-weight:600}
.feature p{margin-top:8px;font-size:14px;line-height:20px;color:var(--text)}
.grid-a{top:340px}
.second-title{position:absolute;top:780px;left:0;width:100%;margin:0}
.stats-art{position:absolute;top:880px;left:205px;width:390px;height:300px;background:linear-gradient(180deg,#f6f6f6 0%,#e2e3e5 55%,#c03030 56%,#c03030 62%,#e9eaeb 63%);border-radius:3px}
.stats{position:absolute;top:870px;left:605px;width:420px;height:320px}
.stat-label{position:absolute;left:105px;color:var(--ink);font-weight:700;font-size:20px;letter-spacing:.3px}
.stats-text{position:absolute;top:1230px;left:205px;width:800px;text-align:center;font-size:15px;line-height:24px}
.grid-b{top:1370px}

/* management band */
.manage{top:4182px;height:490px;background:linear-gradient(100deg,#2c3138 0%,#4b2226 30%,#7a1f24 45%,#3b434c 70%,#6c7b88 100%)}
.manage-copy{position:absolute;top:120px;left:600px;width:500px}
.manage h2{color:var(--white);font-weight:300;font-size:42px;white-space:nowrap}
.manage p{margin-top:12px;color:var(--white);font-size:17px;line-height:25px;letter-spacing:1.5px;text-transform:uppercase;text-align:right}
.manage .btn{position:absolute;top:296px;left:160px;border-radius:0}

/* cta band */
.cta{top:4672px;height:210px;background:var(--red)}
.cta-text{position:absolute;top:70px;left:165px;color:#f5d6d7;font-size:24px;line-height:34px;letter-spacing:2.5px;text-align:center;text-transform:uppercase}
.cta-btn{position:absolute;top:88px;left:780px;border:2px solid var(--white);color:var(--white);font-size:13px;font-weight:700;letter-spacing:1.5px;text-transform:uppercase;padding:12px 32px}

/* footer */
.footer{top:4882px;height:194px;background:var(--footer)}
.footer .brand{position:absolute;top:70px;left:100px}
.footer-tag{position:absolute;top:104px;left:100px;color:#9a9ca0;font-size:13px}
.socials{position:absolute;top:72px;right:160px;display:flex;gap:22px}
.socials span{width:18px;height:18px;border-radius:50%;background:#d8d9db;display:block}
.footer-rule{position:absolute;top:150px;left:100px;right:100px;height:1px;background:#2e2f33}
.copyright{position:absolute;top:162px;left:100px;color:#6d6f73;font-size:11px}
</style>
</head>
<body>

<header class="section hero">
  <div class="hero-photo" role="img" aria-label="Photograph of a red semi truck on the highway at dusk"></div>
  <nav class="nav">
    <div class="brand">RoadPermitGuard</div>
    <ul class="nav-links">
      <li>Home</li><li>License Monitoring</li><li>About</li><li>Contact</li><li>Login</li>
      <li class="search"><svg width="12" height="12" viewBox="0 0 12 12"><circle cx="5" cy="5" r="3.6" fill="none" stroke="#fff" stroke-width="1.6"/><line x1="7.6" y1="7.6" x2="11" y2="11" stroke="#fff" stroke-width="1.6"/></svg></li>
    </ul>
  </nav>
  <p class="hero-kicker">Monitor your fleet electronically</p>
  <h1>Florida Driver<br>License Monitoring</h1>
  <p class="hero-sub">Get alerts by Email and Online.<br>Never let another unlicensed or unauthorized driver behind the wheel.</p>
  <span class="btn">More information</span>
</header>

<section class="section intro">
  <h2 class="section-title">Monitor your drivers electronically, twenty-four hours a day.</h2>
  <p class="intro-text">How many of your drivers currently have a suspended license? The answer may surprise you. Driving with a suspended license is the most commonly committed offense in America. In 2011, over 1.8 million licenses got suspended in Florida. With just over 15 million drivers, that's 12% of all licensed Florida drivers.</p>
  <div class="intro-art" role="img" aria-label="Illustration of a desktop computer showing the monitoring dashboard beside three trucks"></div>
  <div class="services">
    <div class="service">
      <div class="service-icon"><svg width="28" height="26" viewBox="0 0 28 26"><rect x="2" y="2" width="24" height="16" rx="1" fill="none" stroke="#333" stroke-width="2"/><rect x="11" y="18" width="6" height="4" fill="#333"/><rect x="7" y="22" width="14" height="2" fill="#333"/></svg></div>
      <h3>LICENSE MONITORING</h3>
      <p>Monitor your fleet electronically. Get alerts by email and online. Never let another unlicensed or unauthorized driver behind the wheel.</p>
      <span class="read-more">Read more ⊕</span>
    </div>
    <div class="service">
      <div class="service-icon"><svg width="28" height="24" viewBox="0 0 28 24"><path d="M5 10 L8 3 H20 L23 10 Z" fill="none" stroke="#333" stroke-width="2"/><rect x="2" y="10" width="24" height="8" rx="2" fill="#333"/><rect x="4" y="18" width="4" height="4" fill="#333"/><rect x="20" y="18" width="4" height="4" fill="#333"/><circle cx="7" cy="14" r="1.6" fill="#fff"/><circle cx="21" cy="14" r="1.6" fill="#fff"/></svg></div>
      <h3>PRIVATE SECTOR</h3>
      <p>Monitor your fleet electronically. Get alerts by email and online. Never let another unlicensed or unauthorized driver behind the wheel.</p>
      <span class="read-more">Read more ⊕</span>
    </div>
    <div class="service">
      <div class="service-icon"><svg width="28" height="26" viewBox="0 0 28 26"><path d="M2 8 L14 2 L26 8 Z" fill="#333"/><rect x="4" y="10" width="3" height="11" fill="#333"/><rect x="10" y="10" width="3" height="11" fill="#333"/><rect x="16" y="10" width="3" height="11" fill="#333"/><rect x="22" y="10" width="3" height="11" fill="#333"/><rect x="2" y="22" width="24" height="3" fill="#333"/></svg></div>
      <h3>PUBLIC SECTOR</h3>
      <p>Monitor your fleet electronically. Get alerts by email and online. Never let another unlicensed or unauthorized driver behind the wheel.</p>
      <span class="read-more">Read more ⊕</span>
    </div>
  </div>
</section>

<section class="section question">
  <div class="question-art" role="img" aria-label="Photograph of a white truck cab"></div>
  <p class="question-kicker">Florida Driver License Monitoring Service</p>
  <h2>How many of your drivers currently have a suspended license?</h2>
  <div class="devices-art" role="img" aria-label="Monitor and laptop showing the RoadPermitGuard dashboard"></div>
</section>

<section class="section features">
  <h2 class="section-title first-title">Monitor your Whole Fleet Online</h2>
  <div class="feature-grid grid-a">
    <div class="feature"><h4>✎ Some Feature</h4><p>Track every license status daily and get notified the moment anything changes for one of your drivers.</p></div>
    <div class="feature"><h4>▣ Another amazing feature</h4><p>Review your entire fleet from one dashboard with clear reports on valid, expired and suspended licenses.</p></div>
    <div class="feature"><h4>✔ Feature title</h4><p>Add new drivers in seconds and keep records current without phone calls, paperwork or manual checks.</p></div>
    <div class="feature"><h4>✉ Important feature</h4><p>Receive instant email alerts so managers can act quickly before an unlicensed driver takes the road.</p></div>
    <div class="feature"><h4>◆ Amazing feature</h4><p>Export clean audit logs for insurers and compliance reviews whenever they are needed by your team.</p></div>
    <div class="feature"><h4>▤ Epic title goes here</h4><p>Secure online access for every department, with simple roles for managers, staff and fleet supervisors.</p></div>
  </div>

  <h2 class="section-title second-title">Monitor your Whole Fleet Online</h2>
  <div class="stats-art" role="img" aria-label="Illustration of a semi truck whose trailer reads: 1 of every 10 drivers may have a suspended license"></div>
  <div class="stats">
    <svg width="420" height="320" viewBox="0 0 420 320">
      <line x1="42" y1="60" x2="42" y2="260" stroke="#c4262e" stroke-width="2"/>
      <line x1="42" y1="60" x2="300" y2="60" stroke="#222" stroke-width="1"/>
      <line x1="42" y1="160" x2="300" y2="160" stroke="#222" stroke-width="1"/>
      <line x1="42" y1="260" x2="300" y2="260" stroke="#222" stroke-width="1"/>
      <circle cx="42" cy="60" r="38" fill="#c4262e"/>
      <circle cx="42" cy="160" r="38" fill="#c4262e"/>
      <circle cx="42" cy="260" r="38" fill="#c4262e"/>
      <text x="42" y="68" text-anchor="middle" fill="#fff" font-family="Source Sans 3, Arial, sans-serif" font-weight="700" font-size="24">1.8</text>
      <text x="42" y="168" text-anchor="middle" fill="#fff" font-family="Source Sans 3, Arial, sans-serif" font-weight="700" font-size="22">100%</text>
      <text x="42" y="268" text-anchor="middle" fill="#fff" font-family="Source Sans 3, Arial, sans-serif" font-weight="700" font-size="24">12%</text>
    </svg>
    <span class="stat-label" style="top:32px">MILLION SUSPENSIONS</span>
    <span class="stat-label" style="top:132px">15 MILLION DRIVERS</span>
    <span class="stat-label" style="top:232px">SUSPENSIONS PER YEAR!</span>
  </div>
  <p class="stats-text">How many of your drivers currently have a suspended license? The answer may surprise you. Driving with a suspended license is the most commonly committed offense in America. In 2011, over 1.8 million licenses got suspended in Florida. With just over 15 million drivers, that's 12% of all licensed Florida drivers.</p>
  <div class="feature-grid grid-b">
    <div class="feature"><h4>▦ More features</h4><p>Schedule automatic checks for each driver and see changes highlighted the next time you sign in.</p></div>
    <div class="feature"><h4>▭ Amazing feature</h4><p>Works on desktop, tablet and phone so supervisors can confirm driver status from anywhere at all.</p></div>
    <div class="feature"><h4>▶ Let's make another</h4><p>Simple monthly plans sized for small local fleets, large companies and public agencies in Florida.</p></div>
  </div>
</section>

<section class="section manage" role="img" aria-label="Photograph of a red semi truck driving on a highway">
  <div class="manage-copy">
    <h2>Online Driver Management</h2>
    <p>With RoadPermitGuard, your organization will receive automated, time-critical email alerts as soon as a problem appears on a driver's license.</p>
    <span class="btn">Learn more</span>
  </div>
</section>

<section class="section cta">
  <p class="cta-text">Monitor your drivers electronically,<br>twenty-four hours a day.</p>
  <span class="cta-btn">Track your fleet</span>
</section>

<footer class="section footer">
  <div class="brand">RoadPermitGuard</div>
  <p class="footer-tag">Created by experts in Florida traffic law</p>
  <div class="socials"><span></span><span></span><span></span><span></span><span></span></div>
  <div class="footer-rule"></div>
  <p class="copyright">© 2024 RoadPermitGuard. All rights reserved.</p>
</footer>

</body>
</html>
```